Business Cards for company that supports physicians that do medical research

Need to create a business card for Qorvel Studies (www.qorvelstudies.example), a company devoted to supporting physicians who conduct medical research. The form of the card should match the message of research and information quest. I have provided the logo of the company as an uploaded file. Designs should be simple and slick aimed at very high end clients.

Target Market(s)

Medical doctors that are also researchers

Industry/Entity Type

Medical

Contact Information for Business Card

Should feature logo and fields for personal info:
Name/title
Phone /email

Font styles to use
Serif
Sans Serif

Requirements
Must have
• Qorvel logo and fields for personal info:
• Name: Bertrand Okonfu
• Title: VP Research and Senior Analyst
• Phone: 555-203-4719
• email: info@qorvelstudies.example
Nice to have
• Interesting cards that I've seen:
• 1- all black/charcoal or very dark background
• 2- Plastic - semi-transparent
• 3- non-standard height-width ratios
• 4- Functional cards -- USB drive incorporated
Should not have
• Too busy; needs to stay very simple

```html
<!DOCTYPE html>
<html lang="en">
<head>
<meta charset="utf-8">
<title>Qorvel Studies – Business Card</title>
<link rel="stylesheet" href="https://fonts.googleapis.com/css2?family=Lato:wght@400;700&display=swap">
<style>
  :root {
    --page-bg: #e9e7e3;
    --card-bg: #2b3039;
    --brand-blue: #1e88c9;
    --brand-green: #6cc24a;
    --text-light: #ffffff;
    --rule: #d9dde2;
  }
  * { margin: 0; padding: 0; box-sizing: border-box; }
  html, body {
    width: 1200px;
    height: 1000px;
    overflow: hidden;
    background: var(--page-bg);
    font-family: "Lato", sans-serif;
  }
  .canvas { position: relative; width: 1200px; height: 1000px; }
  .card {
    position: absolute;
    left: 265px;
    width: 667px;
    height: 397px;
    border-radius: 24px;
    background: var(--card-bg);
    box-shadow: 0 4px 14px rgba(0, 0, 0, 0.25);
    color: var(--text-light);
  }
  .card--front { top: 73px; }
  .card--back { top: 532px; }
  .brand-name {
    position: absolute;
    left: 45px;
    top: 176px;
    font-size: 37px;
    font-weight: 400;
    letter-spacing: 1px;
    line-height: 1;
    color: var(--text-light);
    white-space: nowrap;
  }
  .person-name {
    position: absolute;
    left: 371px;
    top: 123px;
    font-size: 22px;
    font-weight: 700;
    line-height: 1;
    color: var(--brand-blue);
  }
  .person-title {
    position: absolute;
    left: 372px;
    top: 153px;
    font-size: 16.5px;
    font-weight: 400;
    line-height: 1;
    color: var(--brand-green);
  }
  .divider {
    position: absolute;
    left: 371px;
    top: 180px;
    width: 296px;
    height: 1px;
    background: var(--rule);
  }
  .contact-list {
    position: absolute;
    left: 371px;
    top: 202px;
    list-style: none;
  }
  .contact-item {
    display: flex;
    align-items: center;
    height: 26px;
    font-size: 16.5px;
    line-height: 1;
  }
  .contact-icon {
    width: 14px;
    height: 14px;
    margin-right: 11px;
    fill: var(--brand-blue);
  }
</style>
</head>
<body>
<div class="canvas">

  <section class="card card--front" aria-label="Business card">
    <div class="brand-name">Qorvel Studies</div>
    <h1 class="person-name">Bertrand Okonfu</h1>
    <p class="person-title">VP Research and Senior Analyst</p>
    <div class="divider"></div>
    <ul class="contact-list">
      <li class="contact-item">
        <svg class="contact-icon" viewBox="0 0 14 14" aria-hidden="true"><path d="M1 4c0-2 2-3 6-3s6 1 6 3v1h-3V4H4v1H1z"/><path d="M3 6h8l1.5 6h-11z"/></svg>
        555-203-4719
      </li>
      <li class="contact-item">
        <svg class="contact-icon" viewBox="0 0 14 14" aria-hidden="true"><path d="M1 3h12v1L7 8 1 4z"/><path d="M1 5.2l6 4 6-4V11H1z"/></svg>
        info@qorvelstudies.example
      </li>
      <li class="contact-item">
        <svg class="contact-icon" viewBox="0 0 14 14" aria-hidden="true"><circle cx="6.5" cy="6.5" r="5.5" fill="none" stroke="#1e88c9" stroke-width="1.6"/><path d="M1 6.5h11M6.5 1c-3 3-3 8 0 11M6.5 1c3 3 3 8 0 11" fill="none" stroke="#1e88c9" stroke-width="1"/></svg>
        www.qorvelstudies.example
      </li>
    </ul>
  </section>

  <section class="card card--back" aria-label="Business card">
    <div class="brand-name">Qorvel Studies</div>
    <h2 class="person-name">Bertrand Okonfu</h2>
    <p class="person-title">VP Research and Senior Analyst</p>
    <div class="divider"></div>
    <ul class="contact-list">
      <li class="contact-item">
        <svg class="contact-icon" viewBox="0 0 14 14" aria-hidden="true"><path d="M1 4c0-2 2-3 6-3s6 1 6 3v1h-3V4H4v1H1z"/><path d="M3 6h8l1.5 6h-11z"/></svg>
        555-203-4719
      </li>
      <li class="contact-item">
        <svg class="contact-icon" viewBox="0 0 14 14" aria-hidden="true"><path d="M1 3h12v1L7 8 1 4z"/><path d="M1 5.2l6 4 6-4V11H1z"/></svg>
        info@qorvelstudies.example
      </li>
      <li class="contact-item">
        <svg class="contact-icon" viewBox="0 0 14 14" aria-hidden="true"><circle cx="6.5" cy="6.5" r="5.5" fill="none" stroke="#1e88c9" stroke-width="1.6"/><path d="M1 6.5h11M6.5 1c-3 3-3 8 0 11M6.5 1c3 3 3 8 0 11" fill="none" stroke="#1e88c9" stroke-width="1"/></svg>
        www.qorvelstudies.example
      </li>
    </ul>
  </section>

</div>
</body>
</html>
```